Basic business card

use my newly created logo - and the phrases (Lower Cost of Test & Accelarated New Product Introduction) - and my new email domain / ID - use at conferences / tradeshows

Industry/Entity Type

semiconductor

Contact Information for Business Card

Daniel K Forde, Owner, communicate via Logo - Lower COT - Cost of Test, Accelerated NPI - New Product Introduction, phone +1 555 613 0946, Chandler, Arizona, USA, daniel.forde@qal-vub.com

Font styles to use
Sans Serif

Requirements
Nice to have
• re-use my logo created via Pixel Harbor last August (#7315926)

```html
<!DOCTYPE html>
<html lang="en">
<head>
<meta charset="utf-8">
<title>QAL-VUB Business Card</title>
<link href="https://fonts.googleapis.com/css2?family=Open+Sans:wght@400;600;700&display=swap" rel="stylesheet">
<style>
  :root {
    --page: #232323;
    --card: #151515;
    --card-back: #121212;
    --pattern-a: #1b1b1b;
    --pattern-b: #242424;
    --brand-slate: #4b5878;
    --blue: #1474c1;
    --orange: #f7941d;
    --text: #f2f2f2;
    --muted: #d9d9d9;
  }
  * { margin: 0; padding: 0; box-sizing: border-box; }
  html, body { width: 1200px; height: 780px; overflow: hidden; }
  body {
    background: var(--page);
    font-family: "Open Sans", Arial, sans-serif;
    position: relative;
  }
  .card {
    position: absolute;
    left: 310px;
    width: 580px;
    height: 332px;
    overflow: hidden;
    box-shadow: 0 10px 28px rgba(0,0,0,0.55);
  }
  .card--back { top: 40px; background: var(--card-back); }
  .card--front { top: 408px; background: var(--card); }

  /* back */
  .back-pattern {
    position: absolute; inset: 0;
    background: linear-gradient(135deg, var(--pattern-b) 0%, var(--pattern-a) 55%, var(--card-back) 100%);
  }
  .back-brand {
    position: absolute; left: 50%; top: 50%;
    transform: translate(-50%, -50%);
    display: flex; align-items: center; gap: 10px;
  }
  .brand-square { width: 16px; height: 16px; background: var(--blue); }
  .brand-name {
    font-weight: 400; color: var(--brand-slate);
    letter-spacing: 1px;
  }
  .back-brand .brand-name { font-size: 22px; }

  /* front */
  .front-brand {
    position: absolute; left: 48px; top: 150px;
    display: flex; align-items: center; gap: 12px;
  }
  .front-brand .brand-square { width: 22px; height: 22px; }
  .front-brand .brand-name { font-size: 38px; }
  .divider {
    position: absolute; left: 318px; top: 58px;
    width: 1px; height: 178px; background: var(--blue);
  }
  .details { position: absolute; left: 342px; top: 52px; color: var(--text); }
  .person-name { font-size: 22px; font-weight: 700; line-height: 1.1; }
  .person-name .first { color: var(--blue); }
  .person-name .last { color: var(--orange); }
  .person-title { font-size: 12.5px; color: var(--muted); margin-top: 2px; }
  .contact-list { list-style: none; margin-top: 20px; }
  .contact-list li {
    display: flex; align-items: center; gap: 8px;
    font-size: 12.5px; line-height: 20px;
  }
  .contact-list svg { width: 12px; height: 12px; flex: none; }
  .address { margin-top: 18px; margin-left: 20px; font-size: 12.5px; line-height: 18px; }
  .swoosh { position: absolute; left: 0; bottom: 0; width: 580px; height: 332px; }
</style>
</head>
<body>

  <section class="card card--back" aria-label="Card back">
    <div class="back-pattern" role="img" aria-label="Faint embossed repeating pattern of the company mark"></div>
    <div class="back-brand">
      <span class="brand-square"></span>
      <span class="brand-name">QAL-VUB</span>
    </div>
  </section>

  <section class="card card--front" aria-label="Card front">
    <div class="front-brand">
      <span class="brand-square"></span>
      <span class="brand-name">QAL-VUB</span>
    </div>

    <div class="divider"></div>

    <div class="details">
      <p class="person-name"><span class="first">Colin</span> <span class="last">Marsh</span></p>
      <p class="person-title">Managing Director</p>
      <ul class="contact-list">
        <li>
          <svg viewBox="0 0 12 12" aria-hidden="true"><path fill="var(--blue)" d="M1 4c0-2 2-3 5-3s5 1 5 3v1H8V4H4v1H1zM3 6h6l1 5H2z"/></svg>
          555 208 4417
        </li>
        <li>
          <svg viewBox="0 0 12 12" aria-hidden="true"><rect x="0.5" y="2" width="11" height="8" fill="var(--blue)"/><path d="M1 2.5l5 4 5-4" stroke="var(--card)" stroke-width="1" fill="none"/></svg>
          hello@qal-vub.com
        </li>
        <li>
          <svg viewBox="0 0 12 12" aria-hidden="true"><circle cx="6" cy="6" r="5.5" fill="var(--blue)"/><path d="M0.5 6h11M6 0.5c-2.5 3-2.5 8 0 11M6 0.5c2.5 3 2.5 8 0 11" stroke="var(--card)" stroke-width="0.8" fill="none"/></svg>
          www.qal-vub.com
        </li>
      </ul>
      <p class="address">40 Ridge Road, Mesa<br>Arizona, Zip 85201</p>
    </div>

    <svg class="swoosh" viewBox="0 0 580 332" aria-hidden="true">
      <path d="M0 332 L0 320 C70 300 200 300 330 294 C440 289 530 280 580 266 L580 332 Z" fill="var(--blue)"/>
      <path d="M6 316 C76 296 204 296 332 290 C442 285 528 276 570 264" stroke="#0a0a0a" stroke-width="3" fill="none"/>
      <path d="M8 312 C78 292 206 292 334 286 C444 281 528 272 568 260" stroke="var(--orange)" stroke-width="4" fill="none"/>
    </svg>
  </section>

</body>
</html>
```